We need 2 design works for ads on Facebook to attract new customers

We create result-oriented solutions for the Swiss real estate industry : www.velorbyte.ch

We will soon launch two ads campaigns on Facebook (carousel)

1) one ad with 3 slides to promote our brokerage software Velorbyte Agent
target = real estate brokers and agencies

2) one ad with 3 slides one to promote our 3D service
target = architects, builders, property developers, general contractors…

Each ad will be a 3 slides'slideshow as the idea is to attract new customers by giving relevant information in a fast way (less than 10sec in total and very few text).

We need a design work for both ads and would like them to match with our current visual identity but not only.
The idea is to mix our current graphic design with modern, simple and dynamic visual content.
We provide you the draft, general idea and some HD files and we expect you to be creative to make our campaigns attractive for our targets.
The logo doesn't have to be on each image.
Please feel free to suggest any design as long as it remains appealing and readable.

Here below, all the documents we supply:

- HD files (with logos, headers, footers,…)
- 3D images

Here below the text for each product (see the Facebook carousel example to understand where each text will appear)

TEXT FOR Velorbyte Agent:

DESCRIPTION:
Découvrez Velorbyte Agent, le logiciel de courtage SANS ABONNEMENT pour publier sur tous les portails immobiliers suisses

SLIDE 1:
text on image :
none

text under image :
Publier sans abonnement (bold)
Rapide, Simple, Sans engagement

SLIDE 2:
text on image :
PUBLICATION AU JOUR/OBJET

text under image :
Renforcez votre visibilité (bold)
Payez uniquement ce que vous consommez

SLIDE 3:
text on image:
50% DE RÉDUCTION* (bold)

text under image:
*sur le logiciel pendant 3 mois (bold)
En savoir plus au 022 481 39 52

TEXT FOR Velorbyte 3D:

DESCRIPTION:
Optimisez vos chances de concrétiser la vente de votre projet immobilier grâce à l'imagerie 3D!

SLIDE 1:
text on image :
Velorbyte 3D

text under image :
Le partenaire idéal (bold)
Pour vos images et animations 3D

SLIDE 2:
text on image :
none

text under image :
Qualité, Rapidité, Compétitivité (bold)
Une équipe composée d'architectes et de designers

SLIDE 3:
text on image:
Une image 360° offerte* (bold)

text under image:
*En savoir plus au 022 481 39 52 (bold)
Nos dernières réalisations sur velorbyte.ch

Target Market(s)

VBA = real estate brokers and agencies

VB3D = target = architects, builders, property developers, general contractors…

Industry/Entity Type

Real Estate Development

Font styles to use
Serif
Sans Serif

Requirements
Must have
• Here are the Facebook ad specs :
• Ihttps://www.plinqo-example.com/business/ads-guide/carousel
Nice to have
• light colors or similar colors to our current visual identity
• esthetic, dynamic, simple and modern design
• responsive design
• expressive visual content
• a fun and playful infographic to facilitate the transmission of information
• Both ads must be "UX design oriented" in order to lead to a call to action (i.e. to contact us by email or phone, to click on the ad to get to know more and to be redirected to our website...).

```html
<!DOCTYPE html>
<html lang="fr">
<head>
<meta charset="utf-8">
<title>Velorbyte 3D – Carousel ad</title>
<link href="https://fonts.googleapis.com/css2?family=Open+Sans:wght@400;600;700&family=Montserrat:wght@500;600&display=swap" rel="stylesheet">
<style>
  :root {
    --page-bg: #f3f2f0;
    --post-bg: #ffffff;
    --card-border: #dcdcdc;
    --caption-bg: #f7f7f7;
    --ink: #1d1d1d;
    --ink-soft: #333333;
    --link-blue: #365899;
    --muted: #90949c;
    --brand-grey: #95a6a4;
  }
  * { box-sizing: border-box; margin: 0; padding: 0; }
  html, body { width: 1200px; height: 1200px; overflow: hidden; }
  body {
    background: var(--page-bg);
    font-family: "Open Sans", Arial, sans-serif;
    color: var(--ink);
    position: relative;
  }
  .ad-post {
    position: absolute;
    left: 40px; top: 300px;
    width: 1120px;
    background: var(--post-bg);
    border: 1px solid var(--card-border);
    border-radius: 4px;
    padding: 14px 14px 0;
  }
  .post-header { display: flex; align-items: center; gap: 10px; }
  .page-avatar { width: 30px; height: 30px; border-radius: 50%; background: var(--brand-grey); }
  .page-name { font-weight: 700; font-size: 13px; color: var(--link-blue); letter-spacing: .3px; }
  .sponsored { font-size: 10px; color: var(--muted); }
  .post-menu { margin-left: auto; }
  .post-text { font-size: 15px; line-height: 20px; margin: 26px 0 28px; color: var(--ink); }
  .carousel { display: flex; gap: 13px; }
  .slide {
    width: 263px; border: 1px solid var(--card-border); background: var(--caption-bg);
  }
  .slide-visual { position: relative; height: 262px; overflow: hidden; }
  .photo { position: absolute; inset: 0; }
  .photo-living { background: linear-gradient(180deg, #cfd8de 0%, #e6ddd0 45%, #d8c8b0 100%); }
  .photo-lounge { background: linear-gradient(180deg, #cdd6dc 0%, #eae1d4 50%, #cbb89b 100%); }
  .photo-dining { background: linear-gradient(180deg, #b9cbd8 0%, #dcdfdc 45%, #4b4845 100%); }
  .brand-plate {
    position: absolute; left: 20px; top: 182px; width: 212px; height: 42px;
    background: #fff; display: flex; align-items: center; justify-content: center;
    font-family: "Montserrat", sans-serif; font-weight: 600; font-size: 20px;
    letter-spacing: 2px; color: #111;
  }
  .offer-badge { position: absolute; left: 67px; top: 95px; }
  .offer-badge text { font-family: "Montserrat", sans-serif; fill: #fff; }
  .slide-end .slide-visual { background: #fff; display: flex; align-items: center; justify-content: center; gap: 12px; }
  .end-square { width: 22px; height: 22px; background: var(--brand-grey); }
  .end-name { font-family: "Montserrat", sans-serif; font-weight: 600; font-size: 28px; color: var(--brand-grey); }
  .slide-caption { height: 63px; padding: 14px 14px 0 16px; font-size: 9.5px; line-height: 13px; color: var(--ink-soft); }
  .slide-caption strong { font-weight: 700; color: var(--ink); }
  .slide-end .slide-caption {
    padding: 6px 0 0 50px; font-family: "Montserrat", sans-serif; font-weight: 500;
    font-size: 16px; line-height: 19px; letter-spacing: .5px; color: var(--ink);
  }
  .post-stats { font-size: 12px; color: var(--link-blue); padding: 16px 0 18px; }
  .post-actions {
    display: flex; gap: 80px; border-top: 1px solid #e5e5e5;
    padding: 14px 24px; font-size: 13px; color: var(--muted); width: 348px;
  }
</style>
</head>
<body>
  <article class="ad-post">
    <header class="post-header">
      <span class="page-avatar"></span>
      <div>
        <div class="page-name">Velorbyte 3D</div>
        <div class="sponsored">Sponsored</div>
      </div>
      <svg class="post-menu" width="14" height="9" viewBox="0 0 14 9"><path d="M1 1l6 6 6-6" fill="none" stroke="#90949c" stroke-width="1.6"/></svg>
    </header>
    <p class="post-text">Optimisez vos chances de concrétiser la vente de<br>votre projet immobilier grâce à l'imagerie 3D!</p>

    <div class="carousel">
      <section class="slide">
        <div class="slide-visual">
          <div class="photo photo-living" role="img" aria-label="3D render of a bright living room with large windows overlooking a lake"></div>
          <div class="brand-plate">VELORBYTE 3D</div>
        </div>
        <div class="slide-caption"><strong>Le partenaire idéal</strong><br>Pour vos images et animations 3D</div>
      </section>

      <section class="slide">
        <div class="slide-visual">
          <div class="photo photo-lounge" role="img" aria-label="3D render of a lounge with beige sofa, floor lamp and lake and mountain view"></div>
        </div>
        <div class="slide-caption"><strong>Qualité, Rapidité, Compétitivité</strong><br>Une équipe composée d'architectes et de designers</div>
      </section>

      <section class="slide">
        <div class="slide-visual">
          <div class="photo photo-dining" role="img" aria-label="3D render of a dining area with dark table, bowl of apples and lake view"></div>
          <svg class="offer-badge" width="90" height="104" viewBox="0 0 90 104">
            <polygon points="45,0 90,26 90,78 45,104 0,78 0,26" fill="#95a6a4" fill-opacity=".9"/>
            <text x="45" y="35" text-anchor="middle" font-size="13" font-weight="500">Une image</text>
            <text x="45" y="63" text-anchor="middle" font-size="23" font-weight="600">360°</text>
            <text x="45" y="83" text-anchor="middle" font-size="13" font-weight="500">offerte</text>
          </svg>
        </div>
        <div class="slide-caption"><strong>En savoir plus au 022 481 39 52</strong><br>Nos dernières réalisations sur velorbyte.ch</div>
      </section>

      <section class="slide slide-end">
        <div class="slide-visual">
          <span class="end-square"></span>
          <span class="end-name">Velorbyte 3D</span>
        </div>
        <div class="slide-caption">See more at :<br>www.velorbyte.ch</div>
      </section>
    </div>

    <div class="post-stats">241 Likes • 12 Comments • 6 Shares</div>
    <footer class="post-actions">
      <span>Like</span><span>Comment</span><span>Share</span>
    </footer>
  </article>
</body>
</html>
```